2021 Summer Ads Hollis Bay Custom Homes

We need a re-design of our summer ad run for our customer, Hollis Bay Custom Homes. They are custom home builders in the mostly rural parts of West Virginia, USA. They are known for their "Forever Home" tagline. We'd like two designed ads with the main difference being just the custom home that's featured. These designs should be for a Zintrola banner like 300 x 250 and square ad like 250 x 250. For inspiration please visit the Hollis Bay Custom Homes website at www dot hollisbaycustomhomes dot com

Target Market(s)

consumers / new home shoppers

Industry/Entity Type

Consumer

Requirements
Must have
• HBCH logo
Price Lock Available!
Custom home pic
Learn more >
small CFRM logo mark

```html
<!DOCTYPE html>
<html lang="en">
<head>
<meta charset="utf-8">
<title>Hollis Bay Custom Homes — Summer Ads</title>
<link rel="stylesheet" href="https://fonts.googleapis.com/css2?family=Poppins:wght@300;400;600;700&display=swap">
<style>
  :root {
    --page: #f2f2f2;
    --white: #ffffff;
    --slate: #4f4f4f;
    --brand-red: #a10c0e;
    --ink: #2b2b2b;
    --photo-sky: #9fb6c6;
    --photo-green: #4f6b3a;
    --photo-house: #dcdcd6;
    --photo-dark: #3a3f3a;
    --barn-red: #8e2a22;
    --badge-blue: #1d3f8f;
  }
  * { box-sizing: border-box; margin: 0; padding: 0; }
  html, body { width: 1200px; height: 607px; overflow: hidden; }
  body {
    background: var(--page);
    font-family: "Poppins", sans-serif;
    position: relative;
  }
  .ad { position: absolute; top: 74px; height: 460px; overflow: hidden; background: var(--white); }

  /* ---------- Banner ad ---------- */
  .ad--banner { left: 63px; width: 550px; }
  .banner__photo {
    position: absolute; left: 103px; top: 116px; width: 447px; height: 344px;
    background: linear-gradient(180deg, var(--photo-sky) 0%, #c9d2cf 30%, var(--photo-house) 50%, #8f958a 72%, var(--photo-green) 100%);
  }
  .banner__stripe { position: absolute; left: 66px; top: 217px; width: 37px; height: 170px; background: var(--brand-red); }
  .banner__band { position: absolute; left: 291px; top: 86px; width: 259px; height: 30px; background: var(--brand-red); }
  .banner__panel {
    position: absolute; left: 0; top: 0; width: 291px; height: 217px;
    background: var(--slate); color: var(--white); padding: 36px 0 0 20px;
  }
  .headline { font-weight: 600; font-size: 31px; line-height: 1.15; }
  .subline { font-weight: 400; font-size: 24px; line-height: 1.2; margin-top: 14px; }
  .banner__cta { display: block; font-weight: 600; font-size: 25px; margin-top: 22px; color: var(--white); text-decoration: none; }
  .banner__badge { position: absolute; left: 36px; top: 382px; }
  .banner__logo { position: absolute; right: 12px; top: 28px; }

  .brand-logo {
    display: flex; align-items: center; gap: 8px;
    font-weight: 700; font-size: 20px; letter-spacing: 1px; color: var(--brand-red);
    white-space: nowrap;
  }
  .brand-logo__mark { width: 16px; height: 16px; background: var(--brand-red); }

  /* ---------- Square ad ---------- */
  .ad--square { left: 677px; width: 460px; }
  .square__photo {
    position: absolute; inset: 0;
    background: linear-gradient(180deg, #6d7269 0%, var(--photo-dark) 38%, #5a3a33 62%, var(--barn-red) 72%, #4b5a43 100%);
  }
  .square__shade { position: absolute; inset: 0; background: rgba(20, 20, 20, 0.35); }
  .square__corner { position: absolute; left: 0; top: 0; }
  .square__logo { position: absolute; left: 8px; top: 24px; }
  .square__logo .brand-logo { font-size: 17px; gap: 6px; }
  .square__logo .brand-logo__mark { width: 13px; height: 13px; }
  .square__cta {
    position: absolute; right: 28px; top: 32px;
    display: flex; align-items: center; gap: 12px;
    color: var(--white); font-size: 26px; font-weight: 400; text-decoration: none;
  }
  .square__copy { position: absolute; left: 32px; top: 422px; transform: translateY(-100%); color: var(--white); }
  .square__copy .headline { font-size: 30px; }
  .square__copy .subline { font-size: 25px; margin-top: 6px; font-weight: 300; }
  .square__badge { position: absolute; right: 30px; top: 368px; }
</style>
</head>
<body>

  <section class="ad ad--banner" aria-label="Banner ad">
    <div class="banner__photo" role="img" aria-label="White custom home with dark roof, cupola and stone base in landscaped garden"></div>
    <div class="banner__stripe"></div>
    <div class="banner__band"></div>
    <div class="banner__panel">
      <h1 class="headline">Forever Home</h1>
      <p class="subline">Price Lock Available</p>
      <a class="banner__cta" href="#">Learn more &gt;</a>
    </div>
    <div class="banner__logo">
      <div class="brand-logo"><span class="brand-logo__mark"></span>HOLLIS BAY</div>
    </div>
    <svg class="banner__badge" width="112" height="76" viewBox="0 0 112 76" aria-label="CFRM member badge">
      <rect x="4" y="4" width="104" height="68" rx="4" fill="var(--badge-blue)"/>
    </svg>
  </section>

  <section class="ad ad--square" aria-label="Square ad">
    <div class="square__photo" role="img" aria-label="Red barn-style custom home with grey roof and cupola in front of dense trees"></div>
    <div class="square__shade"></div>
    <svg class="square__corner" width="170" height="278" viewBox="0 0 170 278">
      <polygon points="0,0 170,0 0,278" fill="var(--white)"/>
    </svg>
    <div class="square__logo">
      <div class="brand-logo"><span class="brand-logo__mark"></span>HOLLIS BAY</div>
    </div>
    <a class="square__cta" href="#">Learn More
      <svg width="38" height="38" viewBox="0 0 38 38" aria-hidden="true">
        <circle cx="19" cy="19" r="16.5" fill="none" stroke="var(--white)" stroke-width="2.5"/>
        <polyline points="16,11 24,19 16,27" fill="none" stroke="var(--white)" stroke-width="2.5" stroke-linecap="round" stroke-linejoin="round"/>
      </svg>
    </a>
    <div class="square__copy">
      <h2 class="headline">Forever Home</h2>
      <p class="subline">Price Lock Available</p>
    </div>
    <svg class="square__badge" width="90" height="64" viewBox="0 0 90 64" aria-label="CFRM member badge">
      <rect x="2" y="2" width="86" height="60" rx="4" fill="var(--white)" fill-opacity="0.9"/>
    </svg>
  </section>

</body>
</html>
```